We need a web page design for a new company called "Brambel". We provide an innovative music sharing mobile application that allows music listeners to share their music without paying for a monthly subscription. We would like to incorporate the attached logo and color scheme. The final design should communicate music gifting and sharing.

Industry/Entity Type

It Company

```html
<!DOCTYPE html>
<html lang="en">
<head>
<meta charset="utf-8">
<title>Brambel – Own The Music</title>
<link href="https://fonts.googleapis.com/css2?family=Hind:wght@400;500;600;700&display=swap" rel="stylesheet">
<style>
:root{
  --green:#5fa806;
  --green-dark:#2b3f0b;
  --green-olive:#4a6e12;
  --white:#ffffff;
  --ink:#111111;
  --body:#333333;
  --grey-btn:#444444;
  --footer-bg:#f4f4f4;
  --store:#24380a;
}
*{margin:0;padding:0;box-sizing:border-box}
html,body{width:1077px;height:1200px;overflow:hidden;background:var(--white)}
body{font-family:"Hind",Arial,sans-serif}
.page{position:relative;width:1200px;height:1337px;transform:scale(.8975);transform-origin:0 0}
.hero-bg{position:absolute;left:0;top:0;width:1200px;height:760px}
.brand{position:absolute;left:78px;top:68px;display:flex;align-items:center;gap:14px;color:var(--white)}
.brand-dot{width:50px;height:50px;border-radius:50%;background:var(--white)}
.brand-name{font-size:56px;font-weight:600;line-height:1}
.social{position:absolute;left:1003px;top:42px;display:flex;gap:16px}
.social span{width:23px;height:23px;border-radius:50%;background:var(--white);display:block}
.nav{position:absolute;left:448px;top:82px;display:flex;list-style:none}
.nav a{display:block;color:var(--white);text-decoration:none;font-size:19px;font-weight:500;height:39px;line-height:40px;padding:0 9px}
.nav .active{background:var(--white);color:var(--green);padding:0 16px 0 27px;box-shadow:0 4px 6px rgba(0,0,0,.2)}
.nav li:nth-child(3) a{margin-left:12px}
.hero-copy{position:absolute;left:122px;top:205px;width:345px;color:var(--white)}
.hero-title{font-size:78px;font-weight:700;line-height:.95}
.hero-sub{font-size:34px;font-weight:400;line-height:1;margin-bottom:18px}
.hero-text{font-size:14px;line-height:24px}
.cta{position:absolute;left:122px;top:473px;width:259px;height:55px;border:3px solid #8fd13a;border-radius:3px;background:linear-gradient(#4a8f06,#2e5f02);color:var(--white);font-size:25px;font-weight:700;text-align:center;line-height:54px;box-shadow:0 4px 0 #2a4d05;text-decoration:none}
.arrow{position:absolute;top:305px}
.video{position:absolute;left:475px;top:187px;width:573px;height:341px;background:var(--white);padding:5px}
.video-still{width:100%;height:100%;background:radial-gradient(ellipse at 40% 10%,#e7ecdf 0%,#7ea0b4 25%,#2c3f5a 55%,#0c1426 100%);position:relative}
.play{position:absolute;left:246px;top:124px}
.shadow{position:absolute;left:480px;top:530px;width:570px;height:40px;background:radial-gradient(ellipse at 50% 0%,rgba(30,60,0,.55),rgba(30,60,0,0) 70%)}
.store{position:absolute;top:574px;width:198px;height:67px;background:var(--store);border:2px solid #8fd13a;border-radius:4px;color:var(--white);padding:9px 0 0 22px}
.store.ios{left:543px}
.store.droid{left:750px}
.store small{display:block;font-size:15px;line-height:18px}
.store strong{display:block;font-size:28px;font-weight:500;line-height:32px}
.features{position:absolute;left:0;top:795px;width:1200px}
.feature{position:absolute;width:300px;text-align:center}
.feature-icon{width:172px;height:172px;border-radius:50%;background:var(--green);margin:0 auto;display:flex;align-items:center;justify-content:center}
.feature h2{font-size:19px;font-weight:700;color:var(--ink);margin-top:20px}
.feature p{font-size:14px;line-height:24px;color:var(--body);margin-top:18px;padding:0 12px}
.read-more{display:inline-block;margin-top:16px;width:99px;height:33px;line-height:35px;background:var(--grey-btn);color:var(--white);font-size:14px;font-weight:700;text-decoration:none}
.footer{position:absolute;left:0;top:1233px;width:1200px;height:104px;background:var(--footer-bg);text-align:center;color:var(--ink)}
.footer-nav{margin-top:20px;font-size:17px}
.footer-nav a{color:var(--ink);text-decoration:none;margin:0 14px}
.copyright{margin-top:12px;font-size:16px}
</style>
</head>
<body>
<div class="page">
  <svg class="hero-bg" viewBox="0 0 1200 760" aria-hidden="true">
    <defs>
      <radialGradient id="glow" cx="600" cy="180" r="160" gradientUnits="userSpaceOnUse">
        <stop offset="0" stop-color="#a6d51a"/><stop offset="1" stop-color="#5fa806" stop-opacity="0"/>
      </radialGradient>
    </defs>
    <polygon points="0,0 1200,0 1200,686 660,748 460,698 0,662" fill="#5fa806"/>
    <rect x="400" y="20" width="400" height="300" fill="url(#glow)"/>
    <polygon points="1200,618 1200,686 660,748 460,698 660,720" fill="#4a6e12"/>
    <polygon points="0,622 460,698 245,724 0,662" fill="#2b3f0b"/>
  </svg>

  <div class="brand"><span class="brand-dot"></span><span class="brand-name">Brambel</span></div>
  <div class="social" aria-label="Social links"><span></span><span></span><span></span></div>
  <ul class="nav">
    <li><a class="active" href="#">Home</a></li>
    <li><a href="#">About Brambel</a></li>
    <li><a href="#">Music Colletions</a></li>
    <li><a href="#">Shared Musics</a></li>
    <li><a href="#">Contact Us</a></li>
  </ul>

  <svg class="arrow" style="left:64px" width="40" height="80" viewBox="0 0 40 80" aria-hidden="true"><polyline points="36,2 2,40 36,78" fill="none" stroke="#fff" stroke-width="2"/></svg>
  <svg class="arrow" style="left:1098px" width="40" height="80" viewBox="0 0 40 80" aria-hidden="true"><polyline points="4,2 38,40 4,78" fill="none" stroke="#fff" stroke-width="2"/></svg>

  <div class="hero-copy">
    <h1 class="hero-title">Brambel</h1>
    <p class="hero-sub">Own The Music</p>
    <p class="hero-text">Lorem Ipsum is simply dummy text of the printing and typesetting industry. Lorem Ipsum has been the industry's standard dummy text ever since the 1500s, when an unknown printer took a galley of type and scrambled it to make a type specimen book.</p>
  </div>
  <a class="cta" href="#">Get Started</a>

  <div class="video">
    <div class="video-still" role="img" aria-label="Concert crowd with raised hands under stage lights">
      <svg class="play" width="76" height="76" viewBox="0 0 76 76" aria-hidden="true">
        <circle cx="38" cy="38" r="34" fill="rgba(0,0,0,.35)" stroke="#fff" stroke-width="5"/>
        <polygon points="30,24 54,38 30,52" fill="#fff"/>
      </svg>
    </div>
  </div>
  <div class="shadow"></div>

  <a class="store ios" href="#"><small>Download on</small><strong>AppDepot</strong></a>
  <a class="store droid" href="#"><small>Get it on</small><strong>PlayBazaar</strong></a>

  <section class="features">
    <div class="feature" style="left:109px">
      <div class="feature-icon">
        <svg width="94" height="70" viewBox="0 0 94 70" aria-hidden="true">
          <path d="M2 4h26l6 6h50v8H2z" fill="#fff"/>
          <path d="M10 22h84l-6 46H2z" fill="#fff"/>
          <path d="M50 34v20a5 4 0 1 1-3-3.6V38l8 4v-3z" fill="#5fa806"/>
        </svg>
      </div>
      <h2>Music Sharing</h2>
      <p>Lorem Ipsum is simply dummy text of the printing and typesetting industry. Lorem Ipsum has been the industry's standard dummy text ever since the 1500s .</p>
      <a class="read-more" href="#">Read More</a>
    </div>
    <div class="feature" style="left:450px">
      <div class="feature-icon">
        <svg width="62" height="62" viewBox="0 0 62 62" aria-hidden="true">
          <line x1="12" y1="31" x2="50" y2="10" stroke="#fff" stroke-width="6"/>
          <line x1="12" y1="31" x2="50" y2="52" stroke="#fff" stroke-width="6"/>
          <circle cx="12" cy="31" r="10" fill="#fff"/>
          <circle cx="50" cy="10" r="10" fill="#fff"/>
          <circle cx="50" cy="52" r="10" fill="#fff"/>
        </svg>
      </div>
      <h2>Sharing</h2>
      <p>Lorem Ipsum is simply dummy text of the printing and typesetting industry. Lorem Ipsum has been the industry's standard dummy text ever since the 1500s.</p>
      <a class="read-more" href="#">Read More</a>
    </div>
    <div class="feature" style="left:813px">
      <div class="feature-icon">
        <svg width="66" height="66" viewBox="0 0 66 66" aria-hidden="true">
          <path d="M33 16c-4-10-16-12-16-5 0 4 8 5 16 5zm0 0c4-10 16-12 16-5 0 4-8 5-16 5z" fill="none" stroke="#fff" stroke-width="4"/>
          <rect x="1" y="18" width="29" height="12" fill="#fff"/><rect x="36" y="18" width="29" height="12" fill="#fff"/>
          <rect x="5" y="34" width="25" height="30" fill="#fff"/><rect x="36" y="34" width="25" height="30" fill="#fff"/>
        </svg>
      </div>
      <h2>Gifting Totally Free</h2>
      <p>Lorem Ipsum is simply dummy text of the printing and typesetting industry. Lorem Ipsum has been the industry's standard dummy text ever since the 1500s.</p>
      <a class="read-more" href="#">Read More</a>
    </div>
  </section>

  <footer class="footer">
    <nav class="footer-nav">
      <a href="#">Home</a>|<a href="#">About Brambel</a>|<a href="#">Music Colletions</a>|<a href="#">Shared Musics</a>|<a href="#">Contact Us</a>
    </nav>
    <p class="copyright">© 2014 Company Name ,All Rights Reserved</p>
  </footer>
</div>
</body>
</html>
```